Brochure for a website accessibility report

This brochure is related to a report that www.qelvantrix.org sell. The report shows the results of an automated audit of a websites accessibility. It shows details of issues found with screen shots, examples of code and provides remediation advice.

The brochure will be a pdf 8.5 inches by 11 inches. It can be anywhere from 6 to 10 pages.

The FlintVue™ name itself should be “Bree Serif” font. The fonts, styles, colors and sizes are up to you.

The images used and logo of the Office of Digital Reachworks and K7P logo are upload

We highlighted in blue page extracts from the report we sell. Do not use the blue highlight, it is merely there to show you where the specific examples of the report we sell are vs the other content in the report. The areas in blue which show the content from the actual report should be shown as an extract of the actual page of the report. You have flexibility to change the layout and the way the content look.

The red square callouts over the blue content are callouts that describe the specific page extracts. We used it as a red callout only so that you would be able to see it. You should change the specific location, look and feel of the callout to be appropriate

Target Market(s)

Marketing and Technical people

Industry/Entity Type

Information Technology

Font styles to use
Sans Serif

Colors

Designer to choose colors to be used in the design.

Requirements
Should not have
• wheelchairs, images of blind people

```html
<!DOCTYPE html>
<html lang="en">
<head>
<meta charset="utf-8">
<title>FlintVue™ Accessibility Report Brochure</title>
<link href="https://fonts.googleapis.com/css2?family=Bree+Serif&family=Roboto:wght@300;400;500&display=swap" rel="stylesheet">
<style>
  :root {
    --paper: #f9f8f4;
    --ink: #3b3b3b;
    --ink-dark: #1f1f1f;
    --sand: #e9c993;
    --green: #28b070;
    --green-text: #2aab63;
    --card: #ffffff;
    --bullet: #f2c98c;
    --brand-blue: #1d5ea8;
  }
  * { box-sizing: border-box; margin: 0; padding: 0; }
  html, body { width: 928px; height: 1200px; overflow: hidden; background: var(--paper); }
  .page {
    position: relative; width: 928px; height: 1200px; overflow: hidden;
    background: var(--paper); font-family: "Roboto", Arial, sans-serif; color: var(--ink);
  }
  .intro {
    position: absolute; left: 52px; top: 80px; width: 824px;
    font-size: 16.3px; font-weight: 300; line-height: 20px; color: var(--ink);
  }
  .standards-mark {
    position: absolute; left: 53px; top: 208px; display: flex; align-items: center; gap: 8px;
    font-family: "Roboto", Arial, sans-serif; font-weight: 500; font-size: 20px; color: var(--brand-blue);
  }
  .standards-mark .square { width: 14px; height: 14px; background: var(--brand-blue); }
  .lead {
    position: absolute; left: 52px; top: 278px; font-size: 16.5px; font-weight: 300; color: var(--ink);
  }
  .principle {
    position: absolute; background: var(--card); border-radius: 24px;
    box-shadow: 0 4px 14px rgba(0,0,0,0.07); padding: 30px 32px 0 32px;
  }
  .principle .label { font-size: 13.5px; font-weight: 400; color: var(--ink-dark); letter-spacing: 0.1px; }
  .principle .label b { font-weight: 500; }
  .principle h2 {
    font-family: "Bree Serif", Georgia, serif; font-weight: 400; font-size: 31px;
    color: var(--sand); margin: 4px 0 10px; line-height: 1.15;
  }
  .principle p { font-size: 15px; font-weight: 400; line-height: 18.5px; color: var(--ink-dark); }
  .principle p.note { color: var(--green-text); margin-top: 9px; font-weight: 400; }
  .p1 { left: 52px; top: 328px; width: 395px; height: 218px; }
  .p2 { left: 480px; top: 328px; width: 395px; height: 205px; }
  .p3 { left: 52px; top: 580px; width: 395px; height: 208px; }
  .p4 { left: 481px; top: 568px; width: 394px; height: 220px; }
  .offer {
    position: absolute; left: 52px; top: 840px; width: 876px; height: 360px;
    background: var(--green); border-top-left-radius: 68px; padding: 56px 52px 0 51px; color: #fff;
  }
  .offer .headline {
    font-family: "Bree Serif", Georgia, serif; font-size: 15.6px; line-height: 20px;
    text-align: justify; letter-spacing: 0.1px;
  }
  .offer .body { margin-top: 22px; font-size: 14.6px; font-weight: 300; line-height: 18px; text-align: justify; }
  .offer ul { list-style: none; margin-top: 22px; }
  .offer li { position: relative; padding-left: 32px; font-size: 14.6px; font-weight: 300; line-height: 18px; margin-bottom: 18px; text-align: justify; }
  .offer li::before { content: ""; position: absolute; left: 0; top: 5px; width: 6px; height: 6px; background: var(--bullet); }
</style>
</head>
<body>
<div class="page">
  <p class="intro">The Americans with Disabilities Act (ADA) is a comprehensive federal civil rights law prohibiting discrimination on the basis of disability, enforced by the Department of Justice (DOJ). The ADA prohibits discriminatory lack of access for individuals with disabilities to goods and services of public services and accommodations. Websites are considered places of public accommodations. The DOJ currently uses WCAG 2.1 Level A/AA as an accepted standard by which to measure a website’s accessibility.</p>

  <div class="standards-mark"><span class="square"></span><span>K7P Open Grid Standards Council</span></div>

  <p class="lead">WCAG 2.1 Level A/AA consists of 13 guidelines with 50 checkpoints that are organized under four principles:</p>

  <section class="principle p1">
    <div class="label">PRINCIPLE <b>1</b></div>
    <h2>Perceivable</h2>
    <p>Information and user interface components must be presented to users in ways they can perceive. This means that users must be able to compre-hend the information being depicted:</p>
    <p class="note">It can’t be invisible to all their senses.</p>
  </section>

  <section class="principle p2">
    <div class="label">PRINCIPLE <b>2</b></div>
    <h2>Operable</h2>
    <p>User interface components and navigation must be operable:</p>
    <p class="note">The interface cannot require interaction that a user cannot perform.</p>
  </section>

  <section class="principle p3">
    <div class="label">PRINCIPLE <b>3</b></div>
    <h2>Understandable</h2>
    <p>Information and the operation of a user interface must be understandable:</p>
    <p class="note">Users must be able to understand the information as well as the operation of the user interface.</p>
  </section>

  <section class="principle p4">
    <div class="label">PRINCIPLE <b>4</b></div>
    <h2>Robust</h2>
    <p>Content must be robust enough that it can be interpreted reliably by a wide variety of user agents, including assistive technologies:</p>
    <p class="note">As technologies and user agents evolve, the content should remain accessible.</p>
  </section>

  <section class="offer">
    <p class="headline">Start your journey to a fully compliant website with FlintVue™. This detailed compliance and remediation report is generated based on scanning your website against hundreds of carefully-crafted rules, logging failures, and then generating feedback and recommendations on how to fix the problems based on our years of experience and proven best practices.</p>
    <p class="body">The FlintVue™ report is designed to be shared with your executive team and stakeholders. It is divided into two sections to build knowledge and self-sufficiency.</p>
    <ul>
      <li>The first section provides a detailed analysis of your website per the WCAG 2.1 A/AA principles and includes an at-a-glance Summary Chart for your executive team.</li>
      <li>The second section is designed specifically for your website development team, providing them with detailed examples of problematic issues, suggested ways to fix them, and links for more detailed training.</li>
    </ul>
  </section>
</div>
</body>
</html>
```